Präsentationsvorlagen für Automotive Engineering
Zielgruppe
Automotive Engineering - Software & Embedded systems are main focus including V-Modell
Aufgabenstellung
see Logo

```html
<!DOCTYPE html>
<html lang="en">
<head>
<meta charset="utf-8">
<title>VELOTRA – Presentation Template</title>
<link href="https://fonts.googleapis.com/css2?family=Oswald:wght@400;500;600&family=Open+Sans:wght@400;600&display=swap" rel="stylesheet">
<style>
:root{
  --navy:#1f3a6e;
  --navy-deep:#162b55;
  --red:#e8373c;
  --red-dark:#c8232b;
  --ink:#3d3d3d;
  --muted:#7a7a7a;
  --paper:#ffffff;
  --stage:#141414;
  --stage-top:#0b0b0b;
}
*{margin:0;padding:0;box-sizing:border-box}
html,body{width:1200px;height:2705px;overflow:hidden;background:var(--stage)}
body{position:relative;font-family:"Open Sans",Arial,sans-serif;color:var(--ink)}
.hero-band{position:absolute;left:0;top:0;width:1200px;height:430px;background:var(--stage-top)}
.slide{position:absolute;width:564px;height:317px;overflow:hidden;background:var(--paper)}
.slide svg.bg{position:absolute;inset:0;width:100%;height:100%}
.abs{position:absolute}
.h-title{font-family:"Oswald",Arial,sans-serif;font-weight:500;color:#444;line-height:1.1}
.h-white{color:#fff}
.sub{font-size:10px;color:#555}
.body{font-size:6.5px;line-height:1.85;color:#666}
.body-w{font-size:6.5px;line-height:1.85;color:#f2f2f2}
.red-head{font-family:"Oswald",Arial,sans-serif;font-weight:500;color:var(--red);font-size:11px}
.navy-head{font-family:"Oswald",Arial,sans-serif;font-weight:500;color:var(--navy);font-size:11px}
.brand{font-family:"Oswald",Arial,sans-serif;font-weight:600;color:#fff;letter-spacing:6px;text-align:center}
.tagline{color:var(--red);text-align:center;font-size:11px}
.photo{position:absolute}
.corner-tr{position:absolute;right:0;top:0;width:30px;height:26px;background:var(--red);clip-path:polygon(0 0,100% 0,100% 100%)}
.corner-br{position:absolute;right:0;bottom:0;width:30px;height:26px;background:var(--red);clip-path:polygon(100% 0,100% 100%,0 100%)}
.tag{display:inline-flex;align-items:center;gap:5px;font-size:6.5px;font-family:"Oswald",Arial,sans-serif;color:#444;margin-right:12px}
.tag i{width:8px;height:8px;background:var(--red);display:inline-block}
.agenda-item{position:absolute;left:325px;font-size:6px;color:#666;line-height:1.4}
.agenda-item b{display:block;font-family:"Oswald",Arial,sans-serif;font-weight:500;color:var(--red);font-size:8.5px;margin-bottom:1px}
.center{text-align:center}
.year{font-family:"Oswald",Arial,sans-serif;font-weight:600;color:#fff;font-size:12px}
.stat-label{font-family:"Oswald",Arial,sans-serif;color:var(--red);font-size:9px;text-align:center;width:60px}
.stat-num{font-family:"Oswald",Arial,sans-serif;color:#bbb;font-size:13px;text-align:center;width:60px}
.btn{background:var(--red);color:#fff;font-size:6.5px;padding:6px 14px;display:inline-block}
</style>
</head>
<body>

<div class="hero-band">
  <div class="slide" style="left:365px;top:40px;width:470px;height:272px;background:var(--navy)">
    <div class="photo" role="img" aria-label="Photograph of a car engine in blue tones" style="inset:0;background:radial-gradient(circle at 40% 45%,#2d4c86,#1a3263 70%)"></div>
    <div class="abs brand" style="left:0;width:470px;top:100px;font-size:52px">VELOTRA</div>
    <div class="abs tagline" style="left:0;width:470px;top:178px;font-size:12px">Vehicle Engineering Services</div>
  </div>
</div>

<!-- Row 1 -->
<div class="slide" style="left:23px;top:410px;background:var(--navy)">
  <div class="photo" role="img" aria-label="Photograph of a car engine in blue tones" style="inset:0;background:radial-gradient(circle at 45% 50%,#2e4d88,#1b3263 75%)"></div>
  <div class="abs brand" style="left:0;width:564px;top:112px;font-size:60px">VELOTRA</div>
  <div class="abs tagline" style="left:0;width:564px;top:202px;font-size:14px">Vehicle Engineering Services</div>
</div>

<div class="slide" style="left:614px;top:410px">
  <svg class="bg" viewBox="0 0 564 317"><polygon points="564,40 564,317 352,200" fill="var(--navy)"/><polygon points="564,0 490,0 470,55 564,140" fill="var(--red)"/><polygon points="470,55 564,140 564,40" fill="var(--red-dark)"/></svg>
  <div class="abs h-title" style="left:50px;top:50px;font-size:26px">Welcome Message</div>
  <div class="abs sub" style="left:52px;top:88px">Insert Your Subtitle Here</div>
  <div class="abs body" style="left:52px;top:133px;width:255px">Lorem ipsum dolor sit amet, consectetuer adipiscing elit. Aenean commodo ligula eget dolor. Aenean massa. Cum sociis natoque penatibus et magnis dis parturient montes, nascetur ridiculus mus. Lorem ipsum dolor sit amet, consectetuer adipiscing elit.</div>
  <div class="abs" style="left:52px;top:210px"><span class="tag"><i></i>Machine</span><span class="tag"><i></i>Technology</span><span class="tag"><i></i>Automotive</span><span class="tag"><i></i>Future</span></div>
  <div class="abs" style="left:52px;top:228px"><span class="tag"><i></i>Technician</span><span class="tag"><i></i>Technology</span></div>
</div>

<!-- Row 2 -->
<div class="slide" style="left:23px;top:735px">
  <svg class="bg" viewBox="0 0 564 317"><polygon points="30,0 293,0 293,230 161,288 30,230" fill="var(--red)"/>
    <polygon points="30,0 293,0 293,40 30,120" fill="#ee4a4e" opacity=".5"/>
    <line x1="336" y1="95" x2="336" y2="270" stroke="var(--red)" stroke-width="1"/>
    <g fill="var(--red)"><polygon points="322,90 350,90 336,112"/><polygon points="322,131 350,131 336,153"/><polygon points="322,172 350,172 336,194"/><polygon points="322,213 350,213 336,235"/><polygon points="322,256 350,256 336,278"/></g>
    <g fill="#fff" font-family="Oswald,Arial,sans-serif" font-size="6.5" text-anchor="middle"><text x="336" y="100">01</text><text x="336" y="141">02</text><text x="336" y="182">03</text><text x="336" y="223">04</text><text x="336" y="266">05</text></g>
  </svg>
  <div class="corner-tr"></div><div class="corner-br"></div>
  <div class="abs" style="left:131px;top:28px;font-family:Oswald,sans-serif;color:#fff;font-size:52px;line-height:1">&ldquo;</div>
  <div class="abs center" style="left:50px;width:222px;top:78px;font-family:Oswald,sans-serif;font-style:italic;font-weight:400;color:#fff;font-size:15px;line-height:1.3">For me, the '60s in the automotive industry was awesome. The cars are heavy, huge, rolling works of art.</div>
  <div class="abs center body-w" style="left:50px;width:222px;top:146px">A wonderful serenity has taken possession of my entire soul, like these sweet mornings of spring which I enjoy with my whole heart. I am alone, and feel the charm of existence in this spot, which was created for the bliss of souls like mine.</div>
  <div class="abs center" style="left:50px;width:222px;top:210px;font-family:Oswald,sans-serif;font-style:italic;color:#fff;font-size:7px">Marten Holbeck</div>
  <div class="abs h-title" style="left:317px;top:24px;font-size:25px">Presentation Agenda</div>
  <div class="abs sub" style="left:318px;top:58px">Insert Your Subtitle Here</div>
  <div class="agenda-item" style="left:387px;top:90px"><b>Who We Are ?</b>Lorem Ipsum is not simply<br>random text.</div>
  <div class="agenda-item" style="left:387px;top:131px"><b>Our Unique Services</b>Lorem Ipsum is not simply<br>random text.</div>
  <div class="agenda-item" style="left:387px;top:172px"><b>Our Works</b>Lorem Ipsum is not simply<br>random text.</div>
  <div class="agenda-item" style="left:387px;top:213px"><b>Our Market</b>Lorem Ipsum is not simply<br>random text.</div>
  <div class="agenda-item" style="left:387px;top:256px"><b>Our Client</b>Lorem Ipsum is not simply<br>random text.</div>
</div>

<div class="slide" style="left:614px;top:735px">
  <div class="photo" role="img" aria-label="Photograph of an engine workshop in blue tones" style="left:210px;top:53px;width:354px;height:210px;background:linear-gradient(135deg,#2c4a82,#1a3062);clip-path:polygon(100px 0,100% 0,100% 100%,0 100%)"></div>
  <div class="corner-tr"></div><div class="corner-br"></div>
  <div class="abs h-title" style="left:28px;top:38px;font-size:46px;font-weight:600">About Us</div>
  <div class="abs sub" style="left:28px;top:93px">Insert Your Subtitle Here</div>
  <div class="abs body" style="left:28px;top:123px;width:195px">Lorem ipsum dolor sit amet, consectetuer adipiscing elit. Aenean commodo ligula eget dolor. Aenean massa. Cum sociis natoque penatibus et magnis dis parturient montes, nascetur ridiculus mus.</div>
  <div class="abs body" style="left:28px;top:186px;width:195px">Lorem ipsum dolor sit amet, consectetuer adipiscing elit. Aenean commodo ligula eget dolor. Aenean massa. Cum sociis natoque penatibus et magnis dis parturient montes, nascetur ridiculus mus.</div>
  <div class="abs" style="left:28px;top:250px;font-size:6.5px;color:var(--red)">www.velotra-service.com</div>
  <div class="abs brand" style="left:300px;width:254px;top:148px;font-size:38px;letter-spacing:4px">VELOTRA</div>
  <div class="abs tagline" style="left:300px;width:254px;top:204px">Vehicle Engineering Services</div>
</div>

<!-- Row 3 -->
<div class="slide" style="left:614px;top:1066px;background:var(--navy)">
  <div class="photo" role="img" aria-label="Photograph of a technician working on a car in blue tones" style="inset:0;background:linear-gradient(120deg,#1e3769,#2d4b84 60%,#3a5a92)"></div>
  <div class="corner-tr"></div>
  <svg class="bg" viewBox="0 0 564 317">
    <g stroke="var(--red)" stroke-width="3"><line x1="44" y1="88" x2="190" y2="88"/><line x1="44" y1="183" x2="256" y2="183"/><line x1="44" y1="230" x2="256" y2="230"/></g>
    <rect x="60" y="90" width="58" height="36" fill="#fff" opacity=".08"/><rect x="110" y="134" width="58" height="36" fill="#fff" opacity=".08"/><rect x="60" y="183" width="58" height="36" fill="#fff" opacity=".08"/><rect x="110" y="230" width="58" height="36" fill="#fff" opacity=".08"/>
    <g fill="none" stroke="#fff" stroke-width="1.3">
      <ellipse cx="72" cy="113" rx="10" ry="6"/><circle cx="72" cy="113" r="3"/>
      <path d="M120 156 l-8 -8 a4.5 4.5 0 0 1 8 -4 a4.5 4.5 0 0 1 8 4 z"/>
      <rect x="66" y="197" width="12" height="9" transform="rotate(-35 72 201)"/>
      <path d="M114 247 h12 v4 a6 6 0 0 1 -12 0 z M120 257 v4 M116 262 h8"/>
    </g>
  </svg>
  <div class="abs h-title h-white center" style="left:0;width:564px;top:22px;font-size:28px">Vision and Missions</div>
  <div class="abs" style="left:213px;top:80px;width:230px"><div class="h-white" style="font-family:Oswald,sans-serif;font-size:11px">Our Good Vision</div><div class="body-w">Lorem ipsum dolor sit amet, consectetuer adipiscing elit. Aenean commodo ligula eget dolor. Aenean massa.</div></div>
  <div class="abs" style="left:288px;top:126px;width:240px"><div class="h-white" style="font-family:Oswald,sans-serif;font-size:11px">Passion and Hobby</div><div class="body-w">Lorem ipsum dolor sit amet, consectetuer adipiscing elit. Aenean commodo ligula eget dolor. Aenean massa.</div></div>
  <div class="abs" style="left:213px;top:175px;width:230px"><div class="h-white" style="font-family:Oswald,sans-serif;font-size:11px">Good for Financial Condition</div><div class="body-w">Lorem ipsum dolor sit amet, consectetuer adipiscing elit. Aenean commodo ligula eget dolor. Aenean massa.</div></div>
  <div class="abs" style="left:288px;top:221px;width:240px"><div class="h-white" style="font-family:Oswald,sans-serif;font-size:11px">Achievement and Rewards</div><div class="body-w">Lorem ipsum dolor sit amet, consectetuer adipiscing elit. Aenean commodo ligula eget dolor. Aenean massa.</div></div>
</div>

<div class="slide" style="left:23px;top:1066px">
  <div class="corner-tr"></div><div class="corner-br"></div>
  <svg class="bg" viewBox="0 0 564 317">
    <g stroke="var(--red)" stroke-width="1"><line x1="372" y1="0" x2="372" y2="168"/><line x1="434" y1="0" x2="434" y2="198"/><line x1="496" y1="0" x2="496" y2="168"/></g>
    <g fill="#fff" stroke="var(--red)" stroke-width="1.3">
      <path d="M372 184 l-9 -9 a5 5 0 0 1 9 -5 a5 5 0 0 1 9 5 z"/>
      <path d="M427 204 h14 v5 a7 7 0 0 1 -14 0 z M434 216 v5 M429 222 h10"/>
      <rect x="489" y="168" width="13" height="9" transform="rotate(-35 496 172)"/>
    </g>
  </svg>
  <div class="abs h-title" style="left:32px;top:40px;font-size:28px;font-weight:600">Automotive World is Here,<br>Right Now!</div>
  <div class="abs body" style="left:35px;top:119px;width:270px">Lorem ipsum dolor sit amet, consectetuer adipiscing elit. Aenean commodo ligula eget dolor. Aenean massa. Cum sociis natoque penatibus et magnis dis parturient montes, nascetur ridiculus mus. Lorem ipsum dolor sit amet, consectetuer adipiscing elit. Aenean commodo ligula eget dolor.</div>
  <div class="abs body" style="left:35px;top:180px;width:270px">Aenean massa. Cum sociis natoque penatibus et magnis dis parturient montes, nascetur ridiculus mus.</div>
  <div class="abs" style="left:30px;top:218px;font-family:Oswald,sans-serif;font-size:20px;color:#444">+32.523</div>
  <div class="abs" style="left:113px;top:220px"><div style="font-family:Oswald,sans-serif;color:var(--red);font-size:10px">Visitor this year</div><div class="body">A wonderful serenity has taken</div></div>
  <div class="abs btn" style="left:31px;top:257px">www.velotra-service.com</div>
  <div class="abs stat-label" style="left:342px;top:190px">Passion</div><div class="abs stat-num" style="left:342px;top:203px">54</div>
  <div class="abs stat-label" style="left:404px;top:224px">Awards</div><div class="abs stat-num" style="left:404px;top:237px">332</div>
  <div class="abs stat-label" style="left:466px;top:190px">Income</div><div class="abs stat-num" style="left:466px;top:203px">4067</div>
</div>

<!-- Row 4 -->
<div class="slide" style="left:23px;top:1393px">
  <div class="photo" role="img" aria-label="Photograph of an engine bay in red tones" style="left:0;top:0;width:272px;height:317px;background:linear-gradient(160deg,#e84045,#c52a30)"></div>
  <div class="abs" style="left:0;top:0;width:52px;height:317px;background:var(--navy)"></div>
  <div class="abs" style="left:14px;top:140px;transform:rotate(-90deg);transform-origin:left top;font-family:Oswald,sans-serif;color:#fff;font-size:11px;white-space:nowrap">www.velotra-service.com</div>
  <div class="abs" style="left:16px;top:293px;transform:rotate(-90deg);transform-origin:left top;font-family:Oswald,sans-serif;color:#fff;font-size:11px">2017</div>
  <div class="abs h-title h-white center" style="left:52px;width:220px;top:88px;font-size:28px">Our Story</div>
  <div class="abs center" style="left:52px;width:220px;top:134px;font-family:Oswald,sans-serif;font-style:italic;color:#fff;font-size:12px;line-height:1.35">Historical hoiurney start from<br>here until now we success</div>
  <div class="abs center body-w" style="left:62px;width:200px;top:172px">Lorem ipsum dolor sit amet, consectetuer adipiscing elit. Aenean commodo ligula eget dolor. Aenean massa. Cum sociis natoque penatibus montes.</div>
  <div class="abs center" style="left:52px;width:220px;top:226px;color:#fff;font-size:6.5px;font-weight:600">www.velotra-service.com</div>
  <svg class="bg" viewBox="0 0 564 317">
    <line x1="300" y1="148" x2="564" y2="148" stroke="#ddd" stroke-width=".8"/>
    <polygon points="315,132 332,148 315,164" fill="var(--red)"/>
    <polygon points="424,97 474,148 424,199" fill="var(--red)"/>
  </svg>
  <div class="abs year" style="left:429px;top:140px">2017</div>
  <div class="abs red-head center" style="left:370px;width:120px;top:210px">Description</div>
  <div class="abs body center" style="left:370px;width:120px;top:228px">Lorem ipsum dolor sit amet, consectetuer adipiscing elit. Aenean commodo ligula eget dolor.</div>
  <div class="corner-tr"></div><div class="corner-br"></div>
</div>

<div class="slide" style="left:614px;top:1393px">
  <svg class="bg" viewBox="0 0 564 317">
    <line x1="0" y1="148" x2="540" y2="148" stroke="#ddd" stroke-width=".8"/>
    <polygon points="50,97 100,148 50,199" fill="var(--red)"/>
    <polygon points="236,97 286,148 236,199" fill="var(--red)"/>
    <polygon points="422,97 472,148 422,199" fill="var(--red)"/>
    <polygon points="538,132 555,148 538,164" fill="var(--red)"/>
  </svg>
  <div class="abs year" style="left:57px;top:140px">2018</div>
  <div class="abs year" style="left:243px;top:140px">2019</div>
  <div class="abs year" style="left:429px;top:140px">2020</div>
  <div class="abs red-head center" style="left:20px;width:120px;top:210px">Description</div>
  <div class="abs body center" style="left:20px;width:120px;top:228px">Lorem ipsum dolor sit amet, consectetuer adipiscing elit. Aenean commodo ligula eget dolor.</div>
  <div class="abs red-head center" style="left:203px;width:120px;top:210px">Description</div>
  <div class="abs body center" style="left:203px;width:120px;top:228px">Lorem ipsum dolor sit amet, consectetuer adipiscing elit. Aenean commodo ligula eget dolor.</div>
  <div class="abs red-head center" style="left:375px;width:120px;top:210px">Description</div>
  <div class="abs body center" style="left:375px;width:120px;top:228px">Lorem ipsum dolor sit amet, consectetuer adipiscing elit. Aenean commodo ligula eget dolor.</div>
  <div class="corner-tr"></div><div class="corner-br"></div>
</div>

<!-- Row 5 -->
<div class="slide" style="left:23px;top:1723px">
  <div class="photo" role="img" aria-label="Photograph of an industrial robot arm in orange tones" style="left:0;top:0;width:110px;height:317px;background:linear-gradient(180deg,#d9a46a,#b5542a 55%,#3a3a48)"></div>
  <div class="photo" role="img" aria-label="Photograph of an automated car assembly line in warm tones" style="left:452px;top:0;width:112px;height:317px;background:linear-gradient(180deg,#f0b04a,#c2602f 50%,#4a4550)"></div>
  <div class="abs" style="left:110px;top:0;width:342px;height:317px;background:var(--red)"></div>
  <div class="corner-tr"></div>
  <div class="abs h-title h-white center" style="left:110px;width:342px;top:22px;font-size:28px">Services</div>
  <svg class="bg" viewBox="0 0 564 317"><g fill="none" stroke="#fff" stroke-width="1.2">
    <path d="M175 100 a8 8 0 0 1 16 0 M174 99 v6 h4 v-6 z M188 99 v6 h4 v-6 z"/>
    <path d="M174 146 h12 v10 h-12 z M186 149 h5 l3 4 v3 h-8"/><circle cx="178" cy="157" r="2"/><circle cx="190" cy="157" r="2"/>
    <path d="M176 198 h12 v16 h-12 z M179 203 h6 M179 207 h6"/>
    <circle cx="182" cy="257" r="8"/><path d="M182 252 v5 h4"/>
  </g></svg>
  <div class="abs" style="left:215px;top:90px;width:170px"><div class="h-white" style="font-family:Oswald,sans-serif;font-size:10px">Service One</div><div class="body-w">Heaven land. Seed cattle for. Brought multiply don't creature stars.</div></div>
  <div class="abs" style="left:215px;top:142px;width:170px"><div class="h-white" style="font-family:Oswald,sans-serif;font-size:10px">Service Two</div><div class="body-w">Heaven land. Seed cattle for. Brought multiply don't creature stars.</div></div>
  <div class="abs" style="left:215px;top:194px;width:170px"><div class="h-white" style="font-family:Oswald,sans-serif;font-size:10px">Service Three</div><div class="body-w">Heaven land. Seed cattle for. Brought multiply don't creature stars.</div></div>
  <div class="abs" style="left:215px;top:246px;width:170px"><div class="h-white" style="font-family:Oswald,sans-serif;font-size:10px">Service Four</div><div class="body-w">Heaven land. Seed cattle for. Brought multiply don't creature stars.</div></div>
</div>

<div class="slide" style="left:614px;top:1723px">
  <svg class="bg" viewBox="0 0 564 317">
    <polygon points="305,0 545,0 545,228 425,288 305,228" fill="var(--red)"/>
    <g fill="none" stroke="var(--red)" stroke-width="1"><circle cx="68" cy="81" r="5"/><circle cx="68" cy="144" r="5"/><circle cx="68" cy="204" r="5"/></g>
    <g fill="var(--red)"><circle cx="68" cy="81" r="1.6"/><circle cx="68" cy="144" r="1.6"/><circle cx="68" cy="204" r="1.6"/></g>
    <g fill="none" stroke="#fff" stroke-width="2.2">
      <path d="M352 78 h22 v8 a11 11 0 0 1 -22 0 z M363 97 v7 M356 106 h14"/>
      <path d="M400 66 h32 v11 a16 16 0 0 1 -32 0 z M416 93 v9 M406 104 h20"/>
      <path d="M457 78 h22 v8 a11 11 0 0 1 -22 0 z M468 97 v7 M461 106 h14"/>
    </g>
  </svg>
  <div class="abs" style="left:92px;top:73px;width:170px"><div class="red-head">Good Design Spoiler</div><div class="body">A wonderful serenity has taken possession of my entire soul, like these sweet mornings of spring which I enjoy with my whole heart.</div></div>
  <div class="abs" style="left:92px;top:136px;width:170px"><div class="red-head">Fast Car in The World</div><div class="body">A wonderful serenity has taken possession of my entire soul, like these sweet mornings of spring which I enjoy with my whole heart.</div></div>
  <div class="abs" style="left:92px;top:196px;width:170px"><div class="red-head">Category: Strength body</div><div class="body">A wonderful serenity has taken possession of my entire soul, like these sweet mornings of spring which I enjoy with my whole heart.</div></div>
  <div class="abs h-title h-white center" style="left:305px;width:240px;top:142px;font-size:26px">Achievement</div>
  <div class="abs body-w center" style="left:330px;width:190px;top:180px">A wonderful serenity has taken possession of my entire soul, like these sweet mornings of spring which I enjoy with my whole heart.</div>
  <div class="abs center" style="left:305px;width:240px;top:218px;color:#fff;font-size:6.5px;font-weight:600">www.velotra-service.com</div>
  <div class="corner-tr"></div><div class="corner-br"></div>
</div>

<!-- Row 6 -->
<div class="slide" style="left:23px;top:2050px">
  <svg class="bg" viewBox="0 0 564 317">
    <g stroke="#ccc" stroke-width=".8"><line x1="140" y1="110" x2="430" y2="110"/><line x1="140" y1="215" x2="430" y2="215"/><line x1="430" y1="110" x2="430" y2="215"/></g>
    <g fill="var(--red)"><polygon points="88,88 138,88 113,133"/><polygon points="253,88 303,88 278,133"/><polygon points="418,88 468,88 443,133"/></g>
    <g fill="var(--navy)"><polygon points="88,200 138,200 113,245"/><polygon points="253,200 303,200 278,245"/><polygon points="418,200 468,200 443,245"/></g>
    <g fill="none" stroke="#fff" stroke-width="1.2">
      <path d="M108 106 l8 -8 M114 98 a3 3 0 1 1 3 3"/>
      <path d="M272 100 h6 l6 -4 v12 l-6 -4 h-6 z"/>
      <path d="M436 99 h9 v7 h-9 z M445 101 h4 l2 3 v2 h-6"/>
      <path d="M107 214 v7 h4 v-7 z M111 214 l4 -6 v6 h5 l-2 7 h-7"/>
      <path d="M271 213 h14 v5 h-14 z M273 213 l2 -4 h6 l2 4"/>
      <circle cx="443" cy="216" r="5"/><path d="M443 213 v3 h2"/>
    </g>
  </svg>
  <div class="abs h-title center" style="left:0;width:564px;top:18px;font-size:28px;font-weight:600">Creative Process</div>
  <div class="abs sub center" style="left:0;width:564px;top:60px">Insert Your Subtitle Here</div>
  <div class="abs red-head center" style="left:136px;width:120px;top:140px">Description</div>
  <div class="abs body center" style="left:136px;width:120px;top:158px">A wonderful serenity has<br>taken possession</div>
  <div class="abs red-head center" style="left:301px;width:120px;top:140px">Description</div>
  <div class="abs body center" style="left:301px;width:120px;top:158px">A wonderful serenity has<br>taken possession</div>
  <div class="abs navy-head center" style="left:136px;width:120px;top:250px">Description</div>
  <div class="abs body center" style="left:136px;width:120px;top:268px">A wonderful serenity has<br>taken possession</div>
  <div class="abs navy-head center" style="left:301px;width:120px;top:250px">Description</div>
  <div class="abs body center" style="left:301px;width:120px;top:268px">A wonderful serenity has<br>taken possession</div>
  <div class="abs" style="left:524px;top:128px;transform:rotate(90deg);transform-origin:left top;white-space:nowrap"><div class="red-head">Description</div></div>
  <div class="abs" style="left:507px;top:112px;transform:rotate(90deg);transform-origin:left top;white-space:nowrap;font-size:6.5px;color:#666;line-height:1.7">A wonderful serenity has<br>taken possession</div>
  <div class="corner-tr"></div><div class="corner-br"></div>
</div>

<div class="slide" style="left:614px;top:2050px">
  <div class="photo" role="img" aria-label="Photograph of a car engine in red tones" style="left:0;top:0;width:325px;height:317px;background:linear-gradient(150deg,#e9464b,#cf2f35 60%,#b9262c)"></div>
  <div class="abs h-title h-white center" style="left:0;width:325px;top:22px;font-size:28px">Analysis Data</div>
  <svg class="bg" viewBox="0 0 564 317">
    <g fill="#fff" font-size="6.5" font-family="Open Sans,Arial,sans-serif" text-anchor="end">
      <text x="42" y="174">160</text><text x="42" y="188">140</text><text x="42" y="202">120</text><text x="42" y="216">100</text><text x="42" y="230">80</text><text x="42" y="244">60</text><text x="42" y="258">40</text><text x="42" y="272">20</text><text x="42" y="286">0</text>
    </g>
    <line x1="44" y1="284" x2="280" y2="284" stroke="#f4a0a2" stroke-width=".6"/>
    <g fill="#fff" font-size="6.5" text-anchor="middle"><text x="49" y="295">2014</text><text x="87" y="295">2015</text><text x="125" y="295">2016</text><text x="162" y="295">2017</text><text x="200" y="295">2018</text><text x="238" y="295">2019</text><text x="276" y="295">2020</text></g>
    <path d="M87 220 C110 235 125 212 145 198 C165 185 180 205 200 195 C215 187 225 180 238 176" fill="none" stroke="#fff" stroke-width="1.3"/>
    <path d="M87 232 C110 234 120 212 145 200 C170 190 200 186 238 175" fill="none" stroke="var(--navy)" stroke-width="1.3"/>
    <line x1="120" y1="309" x2="132" y2="309" stroke="#fff"/><line x1="160" y1="309" x2="172" y2="309" stroke="var(--navy)"/>
    <g fill="#fff" font-size="6.5"><text x="133" y="311">Services</text><text x="173" y="311">Sales</text></g>
    <g fill="none" stroke="var(--red)" stroke-width="1.4"><circle cx="445" cy="78" r="5"/><path d="M441 83 l-2 6 M449 83 l2 6"/><circle cx="442" cy="184" r="4"/><circle cx="451" cy="186" r="2.5"/></g>
  </svg>
  <div class="abs red-head center" style="left:385px;width:120px;top:98px">Description</div>
  <div class="abs body center" style="left:395px;width:100px;top:116px">A wonderful serenity has taken possession of my entire soul</div>
  <div class="abs red-head center" style="left:385px;width:120px;top:200px">Description</div>
  <div class="abs body center" style="left:395px;width:100px;top:218px">A wonderful serenity has taken possession of my entire soul</div>
  <div class="corner-tr"></div><div class="corner-br"></div>
</div>

<!-- Row 7 -->
<div class="slide" style="left:23px;top:2379px">
  <div class="abs h-title center" style="left:0;width:564px;top:20px;font-size:28px;font-weight:600">Data Analysis</div>
  <div class="photo" role="img" aria-label="Photograph of an engine in blue tones" style="left:0;top:74px;width:564px;height:142px;background:linear-gradient(90deg,#1b3366,#2a4880 50%,#1b3366)"></div>
  <svg class="bg" viewBox="0 0 564 317">
    <g fill="#fff" font-size="6.5" text-anchor="end"><text x="42" y="95">6</text><text x="42" y="111">5</text><text x="42" y="127">4</text><text x="42" y="143">3</text><text x="42" y="159">2</text><text x="42" y="175">1</text><text x="42" y="191">0</text></g>
    <g stroke="#fff" stroke-opacity=".15" stroke-width=".6"><line x1="48" y1="93" x2="540" y2="93"/><line x1="48" y1="109" x2="540" y2="109"/><line x1="48" y1="125" x2="540" y2="125"/><line x1="48" y1="141" x2="540" y2="141"/><line x1="48" y1="157" x2="540" y2="157"/><line x1="48" y1="173" x2="540" y2="173"/></g>
    <g fill="var(--red)">
      <rect x="73" y="120" width="20" height="69"/><rect x="97" y="151" width="20" height="38"/><rect x="121" y="157" width="20" height="32"/>
      <rect x="190" y="149" width="20" height="40"/><rect x="214" y="173" width="20" height="16"/><rect x="238" y="157" width="20" height="32"/>
      <rect x="308" y="173" width="20" height="16"/><rect x="332" y="160" width="20" height="29"/><rect x="356" y="144" width="20" height="45"/>
      <rect x="425" y="117" width="20" height="72"/><rect x="449" y="144" width="20" height="45"/><rect x="473" y="109" width="20" height="80"/>
    </g>
    <line x1="48" y1="189" x2="540" y2="189" stroke="#fff" stroke-opacity=".5" stroke-width=".6"/>
    <g fill="#fff" font-size="6.5" text-anchor="middle"><text x="107" y="201">Category 1</text><text x="224" y="201">Category 2</text><text x="342" y="201">Category 3</text><text x="459" y="201">Category 4</text></g>
  </svg>
  <div class="abs red-head center" style="left:52px;width:110px;top:229px">2001 Periode</div>
  <div class="abs body center" style="left:52px;width:110px;top:245px">A wonderful serenity has taken possession of my entire soul, like these</div>
  <div class="abs red-head center" style="left:167px;width:110px;top:229px">2002 Periode</div>
  <div class="abs body center" style="left:167px;width:110px;top:245px">A wonderful serenity has taken possession of my entire soul, like these</div>
  <div class="abs red-head center" style="left:287px;width:110px;top:229px">2003 Periode</div>
  <div class="abs body center" style="left:287px;width:110px;top:245px">A wonderful serenity has taken possession of my entire soul, like these</div>
  <div class="abs red-head center" style="left:404px;width:110px;top:229px">2004 Periode</div>
  <div class="abs body center" style="left:404px;width:110px;top:245px">A wonderful serenity has taken possession of my entire soul, like these</div>
  <div class="corner-tr"></div><div class="corner-br"></div>
</div>

<div class="slide" style="left:614px;top:2379px;background:var(--navy)">
  <div class="photo" role="img" aria-label="Photograph of a car factory hall in blue tones" style="inset:0;background:linear-gradient(120deg,#2a4680,#1c3466 60%,#223d74)"></div>
  <svg class="bg" viewBox="0 0 564 317">
    <polygon points="0,0 150,0 150,317 0,317" fill="var(--red)" opacity=".25"/>
    <polygon points="0,40 150,165 0,317" fill="var(--red)"/>
    <polygon points="0,0 95,0 150,165 0,40" fill="#ef5054" opacity=".85"/>
  </svg>
  <div class="abs brand" style="left:290px;width:200px;top:72px;font-size:34px;letter-spacing:3px;text-align:left">VELOTRA</div>
  <div class="abs tagline" style="left:294px;top:118px;text-align:left;font-size:10px">Vehicle Engineering Services</div>
  <div class="abs h-title h-white" style="left:295px;top:143px;font-size:26px;font-weight:600;line-height:1.2">THANK YOU AND SEE<br>YOU NEXT TIME</div>
  <div class="abs body-w" style="left:295px;top:212px;width:215px">A wonderful serenity has taken possession of my entire soul, like these sweet mornings of spring which I enjoy with my heart</div>
  <div class="abs" style="left:295px;top:240px;color:#fff;font-size:6.5px">www.velotra-service.com</div>
</div>

</body>
</html>
```